Wordpress Powered Website. Outstanding Design Required. Using Morvenic Theme

Designers will not need to create anything other than the home page but there are some design elements on the home page which also need to be factored in: 6 product place holders and 2-3 slides for a slideshow (with images I provide).

Designers will need to familiarise themselves with the Morvenic theme to make sure that their design will work within the theme.

The winning designer will set up all the pages and navigation in place. This includes social media icons, favicon, widgets, etc. In other words, the home page needs to be designed and coded and the other preset theme pages need to be organised in a way that we can start using the website on completion of the job.

Most of the designs I had last time were too colourful. This needs to be subtle not in your face.

Background to the business/website:
Ridgeway Banners is a new Australian venture which will sell large format printed banners and other signage. The market is very competitive so it is important to stand out visually and to have a website which is clean, easy to navigate and easy to order. It will be a combination of online sales and assisted sales but all sales enquiries will come from the website.

As our business is focused on presentation it is vital to have excellent design.
Purchased theme is Morvenic. Only this theme is to be used.

1. A home page using all the preset features of the Morvenic theme - it will just be basically taking my wireframe and inputting it to the live theme.
2. A three slide slideshow, ideally with an edited video. The static image slides can be provided by me during the handover. Placeholder for now.
Similar to this one: http://thecedarhollow.example.au/

Attached is the logo which must be utilised, although it could also sit on a dark background. There is our mascot as well which can be used but does not have to be included.

Target Market(s)

Primarily B2B (business to business)
Main industries will be Construction, Retail, Community, Events & Trade Shows

Industry/Entity Type

Printing

Coding

Coded - Design and coding required

Font styles to use
Sans Serif

Requirements
Must have
• Must have the design files made to web pages within the Wordpress environment.
Nice to have
• Clean design. Stand out from competitors based on design.
Should not have
• Should not look like any competitor

```html
<!DOCTYPE html>
<html lang="en">
<head>
<meta charset="utf-8">
<title>Ridgeway Banners – Home</title>
<link href="https://fonts.googleapis.com/css2?family=Open+Sans:ital,wght@0,400;0,600;0,700;0,800;1,700&family=Oswald:wght@400;500&display=swap" rel="stylesheet">
<style>
:root{
  --ink:#1e1e1e;
  --text:#3a3a3a;
  --muted:#6b6b6b;
  --black:#111;
  --panel:#f3f3f3;
  --blue:#1a6fc4;
  --red:#e3141b;
  --yellow:#f6d20e;
  --green:#4f9a2c;
  --white:#fff;
}
*{box-sizing:border-box;margin:0;padding:0}
html,body{width:1200px;height:3377px;overflow:hidden}
body{font-family:"Open Sans",Arial,sans-serif;color:var(--text);background:var(--white);position:relative}
.abs{position:absolute}

.topbar{left:0;top:0;width:1200px;height:36px;background:var(--black);color:#fff;font-size:14px}
.social{left:98px;top:11px;display:flex;gap:12px}
.social span{width:14px;height:14px;border-radius:50%;background:#fff;display:block}
.topcontact{right:98px;top:8px;display:flex;gap:34px;font-weight:600}
.topcontact svg{vertical-align:-3px;margin-right:8px}

.header{left:0;top:36px;width:1200px;height:86px;background:#fff}
.brand{left:98px;top:18px;font-weight:800;font-size:26px;color:var(--ink);line-height:1.05;letter-spacing:.5px;display:flex;align-items:center;gap:10px}
.brand i{width:22px;height:22px;background:var(--red);display:block}
.brand small{display:block;font-size:13px;letter-spacing:3px}
.nav{right:110px;top:34px;display:flex;gap:0;font-size:13px;font-weight:600;color:var(--ink)}
.nav a{padding:0 62px;border-left:1px solid #ddd;text-decoration:none;color:inherit}
.nav a:first-child{border:0}

.hero{left:0;top:122px;width:1200px;height:425px;background:linear-gradient(180deg,#4d5a66 0%,#6c7680 45%,#2d3c48 62%,#1b2a36 100%)}
.hero h1{left:100px;top:140px;width:430px;font-family:"Oswald",sans-serif;font-weight:400;font-size:27px;line-height:1.28;color:#fff}
.btn-yellow{left:100px;top:258px;background:var(--yellow);color:var(--ink);font-weight:700;font-size:15px;padding:8px 16px;border-radius:2px}
.collage{left:720px;top:60px;width:470px;height:325px;background:linear-gradient(135deg,#c8d4df,#d96b4a 40%,#e6c14a 75%,#5a7ea8);box-shadow:0 0 0 4px #fff}
.dots{left:100px;top:390px;display:flex;gap:8px}
.dots span{width:13px;height:13px;border:2px solid #dbe3ea;border-radius:50%}
.dots span.on{background:#7fa7d3}

.section-title{width:1200px;text-align:center;font-weight:700;font-size:23px;color:var(--ink);letter-spacing:.5px}

.product{width:299px;height:205px;display:flex;align-items:center;justify-content:center;color:#fff;font-weight:700;font-size:17px;letter-spacing:.5px;text-shadow:0 1px 3px rgba(0,0,0,.6)}

.difference{left:0;top:1152px;width:1200px;height:413px;background:var(--panel)}
.feature{width:240px;text-align:center}
.feature .ic{width:110px;height:110px;border-radius:50%;background:var(--blue);margin:0 auto 36px;display:flex;align-items:center;justify-content:center;box-shadow:0 3px 6px rgba(0,0,0,.2)}
.feature h3{font-size:14px;font-weight:600;color:var(--ink);margin-bottom:30px}
.feature p{font-size:12.5px;line-height:1.55;color:var(--muted)}

.step{width:300px;text-align:center}
.step .ring{width:134px;height:134px;border-radius:50%;background:#3a3a3a;border:6px solid var(--red);margin:0 auto 22px;display:flex;align-items:center;justify-content:center;box-shadow:0 8px 10px rgba(0,0,0,.25)}
.step h3{font-size:14px;font-weight:600;color:var(--ink)}
.connector{display:flex;gap:12px;align-items:center}
.connector span{border-radius:50%;background:#e3e3e3}

.work-band{left:0;top:1900px;width:1200px;height:115px;background:var(--panel)}
.mosaic{left:0;top:2015px;width:1200px;height:415px;display:grid;grid-template-columns:repeat(7,1fr);grid-template-rows:repeat(3,1fr);gap:3px;background:#fff}
.mosaic div{display:flex;align-items:center;justify-content:center;color:#fff;font-weight:600;font-size:16px;text-align:center}

.about-text{left:100px;top:2560px;width:690px;font-size:14px;line-height:1.55;color:var(--text)}
.about-text h4{font-size:15px;font-weight:700;color:var(--ink);margin-bottom:6px}
.about-text p{margin-bottom:18px}

.quote{left:0;top:2870px;width:1200px;height:275px;background:linear-gradient(100deg,#d9c7b3 0%,#efe2cf 30%,#e9d9c2 55%,#e6b9a9 80%,#c99aa8 100%)}
.quote h2{width:1200px;text-align:center;top:42px;color:#fff;font-size:23px;font-weight:700}
.field{background:#fff;height:32px;font-size:12px;color:#555;padding:8px 10px;border:1px solid #ddd}
.btn-red{left:550px;top:198px;width:100px;height:32px;background:var(--red);color:#fff;font-weight:700;font-size:15px;display:flex;align-items:center;justify-content:center}

.support{left:0;top:3145px;width:1200px;height:163px;background:linear-gradient(180deg,#5aa631,#3f8a22)}
.support h2{width:1200px;text-align:center;top:22px;color:#fff;font-style:italic;font-weight:700;font-size:25px}
.channel{top:90px;display:flex;gap:16px;color:#fff}
.channel b{display:block;font-style:italic;font-size:18px}
.channel small{font-size:13px;font-style:italic;opacity:.85}

.footer{left:0;top:3308px;width:1200px;height:69px;background:var(--black);color:#fff;font-size:13px;font-weight:600}
.footer .links{left:100px;top:25px}
.footer .fsocial{left:543px;top:27px;display:flex;gap:14px}
.footer .fsocial span{width:14px;height:14px;border-radius:50%;background:#fff;display:block}
.footer .copy{right:100px;top:25px}
</style>
</head>
<body>

<div class="abs topbar">
  <div class="abs social"><span></span><span></span><span></span><span></span><span></span></div>
  <div class="abs topcontact">
    <span><svg width="16" height="12" viewBox="0 0 16 12"><rect width="16" height="12" fill="#fff"/><path d="M0 0l8 7 8-7" stroke="#111" stroke-width="1.5" fill="none"/></svg>info@ridgewaybanners.example</span>
    <span><svg width="14" height="14" viewBox="0 0 24 24"><path fill="#fff" d="M6.6 10.8a15 15 0 006.6 6.6l2.2-2.2c.3-.3.7-.4 1-.2 1.1.4 2.3.6 3.6.6.6 0 1 .4 1 1V20c0 .6-.4 1-1 1A17 17 0 013 4c0-.6.4-1 1-1h3.5c.6 0 1 .4 1 1 0 1.3.2 2.5.6 3.6.1.3 0 .7-.2 1z"/></svg>123-456-7890</span>
  </div>
</div>

<header class="abs header">
  <div class="abs brand"><i></i><div>RIDGEWAY<small>BANNERS</small></div></div>
  <nav class="abs nav"><a>PRODUCTS</a><a>GET A QUOTE</a><a>CONTACT US</a></nav>
</header>

<section class="abs hero" role="img" aria-label="Harbour city skyline at dusk">
  <h1 class="abs">We Are A New Australian Firm Which Will Sell Large Format Printed Banners And Other Signage Material</h1>
  <div class="abs btn-yellow">CONACT NOW !</div>
  <div class="abs collage" role="img" aria-label="Collage of printed banners, flags and trade show signage"></div>
  <div class="abs dots"><span></span><span class="on"></span><span></span><span></span></div>
</section>

<h2 class="abs section-title" style="top:590px">OUR PRODUCTS</h2>
<div class="abs product" style="left:100px;top:660px;background:linear-gradient(135deg,#8a5a2c,#4a2e18)" role="img" aria-label="Printed fabric banners">BANNERS &amp; FABRICS</div>
<div class="abs product" style="left:449px;top:660px;background:linear-gradient(135deg,#a7a3a0,#6c5f5c)" role="img" aria-label="Stacked printed boards and signs">BOARDS &amp; SIGNS</div>
<div class="abs product" style="left:800px;top:660px;background:linear-gradient(135deg,#6d8aa0,#8c6a4c)" role="img" aria-label="Feather flags on a beach">FLAGS &amp; POS</div>
<div class="abs product" style="left:100px;top:902px;background:linear-gradient(135deg,#7fa26a,#c07a2e)" role="img" aria-label="Self adhesive vinyl with fruit print">SELF ADHESIVE VINYLS</div>
<div class="abs product" style="left:449px;top:902px;background:linear-gradient(135deg,#7a7a7a,#3e3e3e)" role="img" aria-label="Pull up banners in an office">PULL UP BANNERS</div>
<div class="abs product" style="left:800px;top:902px;background:linear-gradient(135deg,#8a5a3c,#5a3522)" role="img" aria-label="Printed posters on a table">POSTERS</div>

<section class="abs difference">
  <h2 class="abs section-title" style="top:35px">OUR DIFFERENCE</h2>
  <div class="abs feature" style="left:92px;top:125px">
    <div class="ic"><svg width="50" height="50" viewBox="0 0 24 24" fill="none" stroke="#fff" stroke-width="2"><circle cx="10" cy="10" r="6"/><path d="M14.5 14.5L20 20"/></svg></div>
    <h3>Attention To Detail</h3>
    <p>Lorem ipsum dolor sit amet, consectetur adipiscing elit. Aenean et dignissim sem, interdum risus.</p>
  </div>
  <div class="abs feature" style="left:350px;top:125px">
    <div class="ic"><svg width="50" height="50" viewBox="0 0 24 24" fill="none" stroke="#fff" stroke-width="2"><circle cx="12" cy="12" r="7"/><circle cx="12" cy="12" r="2.5"/><path d="M12 2v4M12 18v4M2 12h4M18 12h4"/></svg></div>
    <h3>FAST AND FLEXIBLE</h3>
    <p>Lorem ipsum dolor sit amet, consectetur adipiscing elit. Aenean et dignissim sem, interdum risus.</p>
  </div>
  <div class="abs feature" style="left:607px;top:125px">
    <div class="ic"><svg width="50" height="50" viewBox="0 0 24 24" fill="#fff"><path d="M2 10h4v11H2zM8 21V10l5-8c1.5 0 2.5 1 2 3l-1 4h6c1.2 0 2 1 1.8 2.2l-1.6 7.6c-.2.7-.8 1.2-1.5 1.2z"/></svg></div>
    <h3>SECURE DELIVERY</h3>
    <p>Lorem ipsum dolor sit amet, consectetur adipiscing elit. Aenean et dignissim sem, interdum risus.</p>
  </div>
  <div class="abs feature" style="left:866px;top:125px">
    <div class="ic"><svg width="50" height="50" viewBox="0 0 24 24" fill="#fff"><rect x="5" y="7" width="14" height="15" rx="2"/><path d="M9 7V4h6v3" stroke="#fff" stroke-width="2" fill="none"/><text x="12" y="19" font-size="9" text-anchor="middle" fill="#1a6fc4" font-family="Arial">$</text></svg></div>
    <h3>NICE PRICES</h3>
    <p>Lorem ipsum dolor sit amet, consectetur adipiscing elit. Aenean et dignissim sem, interdum risus.</p>
  </div>
</section>

<h2 class="abs section-title" style="top:1605px">OUR PROCESS</h2>
<div class="abs step" style="left:137px;top:1690px">
  <div class="ring"><svg width="44" height="44" viewBox="0 0 24 24" fill="none" stroke="#fff" stroke-width="2"><path d="M14 4H5v16h9"/><path d="M10 12h11M17 8l4 4-4 4"/></svg></div>
  <h3>LOREM IPSUM SIT DOLOR</h3>
</div>
<div class="abs step" style="left:450px;top:1690px">
  <div class="ring"><svg width="44" height="44" viewBox="0 0 24 24" fill="none" stroke="#fff" stroke-width="2"><rect x="5" y="4" width="14" height="17" rx="1"/><path d="M9 4V2h6v2M8 10h8M8 14h8M8 18h5"/></svg></div>
  <h3>LOREM IPSUM SIT DOLOR</h3>
</div>
<div class="abs step" style="left:760px;top:1690px">
  <div class="ring"><svg width="44" height="44" viewBox="0 0 24 24" fill="none" stroke="#fff" stroke-width="2"><path d="M13 3H5v18h12v-6"/><path d="M10 12h11M17 8l4 4-4 4"/></svg></div>
  <h3>LOREM IPSUM SIT DOLOR</h3>
</div>
<div class="abs connector" style="left:385px;top:1748px"><span style="width:10px;height:10px"></span><span style="width:14px;height:14px"></span><span style="width:18px;height:18px"></span><span style="width:24px;height:24px"></span></div>
<div class="abs connector" style="left:697px;top:1748px"><span style="width:10px;height:10px"></span><span style="width:14px;height:14px"></span><span style="width:18px;height:18px"></span><span style="width:24px;height:24px"></span></div>

<div class="abs work-band"><h2 class="abs section-title" style="top:42px">OUR LATEST WORK</h2></div>
<div class="abs mosaic">
  <div style="background:#c7b9a2" role="img" aria-label="Office print display"></div>
  <div style="background:#b7c6d4" role="img" aria-label="Client reviewing prints"></div>
  <div style="background:#9aa3ad;grid-row:span 2" role="img" aria-label="Row of pull up banners"></div>
  <div style="background:#b4a6a2" role="img" aria-label="Printed brochures on desk"></div>
  <div style="background:#d9d2c8;grid-row:span 2" role="img" aria-label="Large number poster"></div>
  <div style="background:#3b4a44" role="img" aria-label="Street signs"></div>
  <div style="background:#8fb3c7;grid-row:span 2" role="img" aria-label="Corporate banners"></div>
  <div style="background:#e7c84a;grid-row:span 2" role="img" aria-label="Colourful poster wall"></div>
  <div style="background:#c49f8a" role="img" aria-label="Fashion print display"></div>
  <div style="background:rgba(40,40,40,.85);grid-row:span 2">LOREM IPSUM<br>DOLOR SIT AMET</div>
  <div style="background:#c86a5a" role="img" aria-label="Window sale signs"></div>
  <div style="background:#9fc68a" role="img" aria-label="Printed flyers"></div>
  <div style="background:#8aa7b0" role="img" aria-label="Printed icon boards"></div>
  <div style="background:#d98b6a" role="img" aria-label="Flags in sunlight"></div>
  <div style="background:#bfe0d2" role="img" aria-label="Green printed leaflets"></div>
</div>

<h2 class="abs section-title" style="top:2482px">ABOUT RIDGEWAY BANNERS</h2>
<div class="abs about-text">
  <h4>OUR LITTLE BUSINESS</h4>
  <p>Lorem ipsum dolor sit amet, consectetur adipiscing elit. Aenean et dignissim sem, interdum risus. Vestibulum consectetur nisi mollis diam pulvinar adipiscing. Vestibulum ut urna nec nibh adipiscing facilisis. Etiam auctor porta lacus ac luctus. Praesent ac libero fermentum, rhoncus magna a, dapibus mauris. Nam ut auctor justo. Sed ante odio, luctus quis nequ nec, adipiscing eleifend arcu. Integer nunc turpis, porttitor at lorem ut.Quisque hendrerit Lorem ipsum dolor sit amet, consectetur adipiscing elit. Aenean et dignissim sem, interdum risus. Vestibulum consectetur nisi mollis diam pulvinar adipiscing. Vestibulum ut urna nec nibh adipiscing facilisis. Etiam auctor porta lacus ac luctus. Praesent ac libero fermentum, rhoncus magna a, dapibus mauris.</p>
  <p>Lorem ipsum dolor sit amet, consectetur adipiscing elit. Aenean et dignissim sem, interdum risus. Vestibulum consectetur nisi mollis diam pulvinar adipiscing. Vestibulum ut urna nec nibh adipiscing facilisis. Etiam auctor porta lacus ac luctus. Praesent ac libero fermentum, rhoncus magna a, dapibus mauris.</p>
</div>
<div class="abs" style="left:838px;top:2558px;width:262px;height:130px;background:linear-gradient(135deg,#d8dde2,#7c8ea8)" role="img" aria-label="Staff member working at a computer"></div>
<div class="abs" style="left:838px;top:2704px;width:262px;height:130px;background:linear-gradient(135deg,#e5e7ea,#3a4250)" role="img" aria-label="Business team group photo"></div>

<section class="abs quote" role="img" aria-label="Soft blurred warm background">
  <h2 class="abs">GET A QUOTE</h2>
  <div class="abs field" style="left:170px;top:100px;width:215px">Name</div>
  <div class="abs field" style="left:400px;top:100px;width:215px">Email</div>
  <div class="abs field" style="left:630px;top:100px;width:400px;height:72px">Your Message</div>
  <div class="abs field" style="left:170px;top:140px;width:215px">Phone Number</div>
  <div class="abs field" style="left:400px;top:140px;width:215px">Enquiry Type<svg style="position:absolute;right:8px;top:12px" width="10" height="7" viewBox="0 0 10 7"><path d="M1 1l4 4 4-4" stroke="#888" fill="none" stroke-width="1.5"/></svg></div>
  <div class="abs btn-red">SUBMIT</div>
</section>

<section class="abs support">
  <h2 class="abs">We're Dedicated to Our Customers 24x7</h2>
  <div class="abs channel" style="left:100px"><svg width="36" height="36" viewBox="0 0 24 24"><path fill="#fff" d="M6.6 10.8a15 15 0 006.6 6.6l2.2-2.2c.3-.3.7-.4 1-.2 1.1.4 2.3.6 3.6.6.6 0 1 .4 1 1V20c0 .6-.4 1-1 1A17 17 0 013 4c0-.6.4-1 1-1h3.5c.6 0 1 .4 1 1 0 1.3.2 2.5.6 3.6.1.3 0 .7-.2 1z"/></svg><div><b>123-456-7890</b><small>Available 24/7 - Call us any time.</small></div></div>
  <div class="abs channel" style="left:418px"><svg width="42" height="32" viewBox="0 0 26 20"><rect x="1" y="1" width="24" height="18" fill="none" stroke="#fff" stroke-width="2"/><path d="M1 1l12 10L25 1" stroke="#fff" stroke-width="2" fill="none"/></svg><div><b>Email Us</b><small>Have a question? Let us help.</small></div></div>
  <div class="abs channel" style="left:725px"><svg width="40" height="34" viewBox="0 0 26 22" fill="none" stroke="#fff" stroke-width="2"><path d="M2 2h14v9H8l-4 3v-3H2z"/><path d="M19 7h5v9h-2v3l-4-3h-6v-3"/></svg><div><b>Live Chat</b><small>Online Support</small></div></div>
  <div class="abs channel" style="left:930px"><svg width="24" height="36" viewBox="0 0 14 22"><path d="M2 6a5 5 0 0110 0c0 4-5 4-5 8" stroke="#fff" stroke-width="3" fill="none"/><circle cx="7" cy="19" r="2" fill="#fff"/></svg><div><b>Help</b><small>Find your answers.</small></div></div>
</section>

<footer class="abs footer">
  <div class="abs links">PRODUCTS &nbsp;/&nbsp; GET A QUOTE &nbsp;/&nbsp; CONTACT US</div>
  <div class="abs fsocial"><span></span><span></span><span></span><span></span><span></span></div>
  <div class="abs copy">© 2016 RIDGEWAY BANNERS. ALL RIGHTS RESERVED.</div>
</footer>

</body>
</html>
```